Business Card Design

We are a manufacturing and distribution company with most of our customer base being supermarkets. We have established brand guidelines that are attached.

```html
<!DOCTYPE html>
<html lang="en">
<head>
<meta charset="utf-8">
<title>Kelvora Business Card</title>
<link href="https://fonts.googleapis.com/css2?family=Arimo:wght@400;700&display=swap" rel="stylesheet">
<style>
  :root {
    --stage: #1c1c1c;
    --card-white: #ffffff;
    --brand-blue: #0a63ae;
    --brand-blue-deep: #0b4f8c;
    --brand-red: #e3202a;
    --ink: #1a1a1a;
    --ink-soft: #2b2b2b;
  }
  * { box-sizing: border-box; margin: 0; padding: 0; }
  html, body { width: 1200px; height: 988px; overflow: hidden; }
  body {
    background: var(--stage);
    font-family: "Arimo", Arial, sans-serif;
    position: relative;
  }
  .card {
    position: absolute;
    width: 540px;
    height: 308px;
    border-radius: 16px;
    overflow: hidden;
    box-shadow: 0 10px 30px rgba(0,0,0,.55);
  }

  /* Back side */
  .card-back {
    left: 50px; top: 150px;
    background: linear-gradient(135deg, #1f78c4 0%, var(--brand-blue) 50%, var(--brand-blue-deep) 100%);
  }
  .card-back .pattern-area {
    position: absolute; inset: 0;
    background: linear-gradient(135deg, #2c84cc 0%, #0a5fa7 55%, #0a4f8e 100%);
  }
  .card-back .back-brand {
    position: absolute; left: 50%; top: 50%;
    transform: translate(-50%, -50%);
    display: flex; align-items: center; gap: 10px;
    color: var(--card-white);
    font-weight: 700; font-size: 30px; letter-spacing: 2px;
  }
  .brand-square {
    width: 22px; height: 22px;
    background: var(--brand-red);
  }

  /* Front side */
  .card-front {
    left: 610px; top: 530px;
    background: var(--card-white);
  }
  .brand {
    position: absolute; right: 34px; top: 46px;
    display: flex; align-items: center; gap: 12px;
    color: var(--ink);
    font-weight: 700; font-size: 42px; letter-spacing: 1px;
  }
  .divider {
    position: absolute; left: 40px; right: 36px; top: 160px;
    height: 1.5px; background: var(--brand-red);
  }
  .person {
    position: absolute; left: 34px; top: 110px;
  }
  .person-name {
    font-weight: 700; font-size: 25px; line-height: 1;
    letter-spacing: .3px;
  }
  .person-name .first { color: var(--brand-red); }
  .person-name .last { color: var(--brand-blue); }
  .person-role {
    margin-top: 4px; margin-left: 18px;
    font-size: 15px; color: var(--ink-soft);
  }
  .contacts {
    position: absolute; left: 50px; top: 178px;
    list-style: none;
    font-size: 15px; color: var(--ink-soft);
  }
  .contacts li {
    display: flex; align-items: center; gap: 8px;
    height: 23px;
  }
  .contacts svg { width: 13px; height: 13px; flex: none; }
  .address {
    position: absolute; right: 34px; top: 178px;
    text-align: right;
    font-size: 14px; line-height: 1.4; color: var(--ink-soft);
  }
  .band {
    position: absolute; left: 0; right: 0; bottom: 0; height: 16px;
  }
</style>
</head>
<body>

  <section class="card card-back" aria-label="Business card, back">
    <div class="pattern-area" role="img" aria-label="Repeating brand pattern on glossy blue"></div>
    <div class="back-brand"><span class="brand-square"></span>KELVORA</div>
  </section>

  <section class="card card-front" aria-label="Business card, front">
    <div class="brand"><span class="brand-square"></span>KELVORA</div>

    <div class="person">
      <p class="person-name"><span class="first">DANIEL</span> <span class="last">REYES</span></p>
      <p class="person-role">CEO/Founder</p>
    </div>

    <div class="divider"></div>

    <ul class="contacts">
      <li>
        <svg viewBox="0 0 16 16" aria-hidden="true"><path fill="#0a63ae" d="M3.6 1.5l2.2 2.6-1.3 1.6c.9 2 2.5 3.6 4.6 4.6l1.6-1.3 2.6 2.2-1.4 2.4C6.6 13.2 2.8 9.4 1.2 3z"/></svg>
        555-014-2286
      </li>
      <li>
        <svg viewBox="0 0 16 16" aria-hidden="true"><rect x="1" y="3" width="14" height="10" fill="#0a63ae"/><path d="M1 3l7 6 7-6" fill="none" stroke="#fff" stroke-width="1.3"/></svg>
        info@kelvora.com.au
      </li>
      <li>
        <svg viewBox="0 0 16 16" aria-hidden="true"><circle cx="8" cy="8" r="7" fill="#0a63ae"/><path d="M1 8h14M8 1c-3 3-3 11 0 14M8 1c3 3 3 11 0 14" fill="none" stroke="#fff" stroke-width="1"/></svg>
        www.kelvora.com.au
      </li>
    </ul>

    <address class="address">
      1204 Marlow Street<br>
      Country Name, AB 40215
    </address>

    <svg class="band" viewBox="0 0 540 16" preserveAspectRatio="none" aria-hidden="true">
      <polygon points="0,0 374,0 368,16 0,16" fill="var(--brand-blue)"/>
      <polygon points="382,0 540,0 540,16 376,16" fill="var(--brand-red)"/>
    </svg>
  </section>

</body>
</html>
```